Pawn & Gun store business card design

Hello! We would like a new business card design for our pawn & gun store. We loan money on items of value and sell firearms, jewelry, electronics & more.

Card will need to have the following information:

Business name - Prairie Nickel Pawn & Gun
Address - 2417 Hwy 53 S. Suite C Harlow Springs, NM 87555
Employees name - Darren Kellum
Phone number - 555-613-8840
Email - PrairieNickelPawn@Mailvera.com
Website - PrairieNickelPawn.com

Somewhere on the card we would like it to say "Offering 10 Month Layaway!" & "We buy & loan on anything of value!". Our main store color is orange (please see logo). Logo does not have to be on the business card but it can be. Would like the back to have an area to write a note on the back. We like vintage things like old coins, collectables, firearms and more so think about this in the design. We want a business card as unique as our store!

Colors

Designer to choose colors to be used in the design.

Requirements
Nice to have
• Vintage Style

```html
<!DOCTYPE html>
<html lang="en">
<head>
<meta charset="utf-8">
<title>Prairie Nickel Pawn &amp; Gun – Business Card</title>
<link rel="stylesheet" href="https://fonts.googleapis.com/css2?family=Roboto:wght@400&family=Roboto+Slab:wght@700&family=Arvo:ital@1&display=swap">
<style>
  :root {
    --bg: #9a9a9a;
    --paper: #eceae8;
    --brown: #3d2518;
    --orange: #e2661f;
    --ink: #5b5b5b;
    --rule: #a9a6a3;
  }
  * { box-sizing: border-box; margin: 0; padding: 0; }
  html, body { width: 1200px; height: 1078px; overflow: hidden; }
  body {
    background: var(--bg);
    display: flex;
    flex-direction: column;
    align-items: center;
    justify-content: center;
    gap: 56px;
    font-family: "Roboto", Arial, sans-serif;
  }
  .card {
    position: relative;
    width: 820px;
    height: 469px;
    background: var(--paper);
    box-shadow: 0 10px 28px rgba(0,0,0,.25);
  }
  .frame {
    position: absolute;
    inset: 26px;
    border: 3px solid var(--brown);
  }
  /* front */
  .brand {
    position: absolute;
    left: 60px;
    top: 0;
    width: 300px;
    height: 100%;
    display: flex;
    align-items: center;
    justify-content: center;
    gap: 12px;
  }
  .brand-dot {
    width: 20px; height: 20px;
    border-radius: 50%;
    background: var(--orange);
    flex: none;
  }
  .brand-name {
    font-family: "Roboto Slab", Georgia, serif;
    font-weight: 700;
    font-size: 28px;
    line-height: 1.1;
    color: var(--orange);
  }
  .divider {
    position: absolute;
    left: 375px;
    top: 120px;
    width: 2px;
    height: 232px;
    background: var(--rule);
  }
  .details {
    position: absolute;
    left: 410px;
    top: 118px;
    color: var(--ink);
    font-size: 18px;
    line-height: 1.4;
  }
  .person {
    font-family: "Roboto Slab", Georgia, serif;
    font-weight: 700;
    font-size: 28px;
    color: var(--orange);
    text-transform: uppercase;
    letter-spacing: 1px;
    margin-bottom: 6px;
  }
  .address { margin-bottom: 10px; }
  .contact { list-style: none; }
  .contact li { display: flex; align-items: center; gap: 10px; }
  .contact svg { width: 16px; height: 16px; flex: none; fill: var(--orange); }
  /* back */
  .card-back .frame { border-bottom: none; }
  .back-base {
    position: absolute;
    left: 26px; right: 26px; bottom: 26px;
    height: 3px;
  }
  .back-base::before, .back-base::after {
    content: "";
    position: absolute;
    top: 0;
    height: 3px;
    background: var(--brown);
  }
  .back-base::before { left: 0; width: 262px; }
  .back-base::after { right: 0; width: 262px; }
  .back-brand {
    position: absolute;
    left: 50%;
    bottom: 34px;
    transform: translateX(-50%);
    display: flex;
    align-items: center;
    gap: 8px;
    white-space: nowrap;
  }
  .back-brand .brand-dot { width: 16px; height: 16px; }
  .back-brand .brand-name { font-size: 20px; }
  .tagline {
    position: absolute;
    font-family: "Arvo", Georgia, serif;
    font-style: italic;
    font-size: 16px;
    line-height: 20px;
    color: var(--brown);
    white-space: nowrap;
  }
  .tagline-left { left: 42px; bottom: 36px; }
  .tagline-right { right: 40px; bottom: 4px; }
</style>
</head>
<body>
  <section class="card card-front">
    <div class="frame"></div>
    <div class="brand">
      <span class="brand-dot"></span>
      <span class="brand-name">Prairie Nickel Pawn</span>
    </div>
    <div class="divider"></div>
    <div class="details">
      <h1 class="person">Darren Kellum</h1>
      <p class="address">Prairie Nickel Pawn &amp; Gun<br>2417 Hwy 53 S.<br>Suite C Harlow Springs, NM 87555</p>
      <ul class="contact">
        <li><svg viewBox="0 0 16 16"><path d="M3.5 1l2.5 3-1.5 2a9 9 0 0 0 5 5l2-1.5 3 2.5-1.5 2.5C7 14.5 1.5 9 1 2.5z"/></svg>555-613-8840</li>
        <li><svg viewBox="0 0 16 16"><path d="M1 3h14v10H1z M1.5 3.5L8 9l6.5-5.5" stroke="#eceae8" stroke-width="1.2"/></svg>PrairieNickelPawn@Mailvera.com</li>
        <li><svg viewBox="0 0 16 16"><circle cx="8" cy="8" r="7"/></svg>www.PrairieNickelPawn.com</li>
      </ul>
    </div>
  </section>

  <section class="card card-back">
    <div class="frame"></div>
    <div class="back-base"></div>
    <p class="tagline tagline-left">Offering 10 Month Layaway</p>
    <div class="back-brand">
      <span class="brand-dot"></span>
      <span class="brand-name">Prairie Nickel Pawn</span>
    </div>
    <p class="tagline tagline-right">We buy &amp; loan on anything of value</p>
  </section>
</body>
</html>
```